Bramblewood Card Company Business Cards

We are a trading card store with Glimmorax, sports and other TCG cards, we need a business card design that encompasses a clean cut, modern style with a retro flare. website is bramblewoodcardco.com for reference. Can utilize a comic book era feel or a more modern outdoor feel to utilize the "Pacific Northwest" elements of tress, mountains, etc.

Industry/Entity Type

Trading cards and collectibles

Contact Information for Business Card

business name, email address, phone number, name, owner job title

Font styles to use
Sans Serif

```html
<!DOCTYPE html>
<html lang="en">
<head>
<meta charset="utf-8">
<title>Bramblewood Card Company – Business Card</title>
<link rel="stylesheet" href="https://fonts.googleapis.com/css2?family=Montserrat:wght@400;500;700;800&display=swap">
<style>
  :root {
    --page-bg: #2a2a2b;
    --card-bg: #1d1d1e;
    --cyan: #29c3e3;
    --grey: #7a7a7c;
    --text: #f2f2f2;
    --rule: #555558;
  }
  html, body {
    margin: 0;
    width: 1200px;
    height: 801px;
    overflow: hidden;
    background: var(--page-bg);
    font-family: "Montserrat", sans-serif;
  }
  .stage {
    position: relative;
    width: 1200px;
    height: 801px;
  }
  .card {
    position: absolute;
    top: 246px;
    width: 540px;
    height: 309px;
    border-radius: 14px;
    overflow: hidden;
    background: var(--card-bg);
    box-shadow: 0 10px 28px rgba(0,0,0,.45);
  }
  .card--front { left: 40px; }
  .card--back  { left: 620px; }

  /* front */
  .brand {
    position: absolute;
    left: 30px;
    top: 150px;
    width: 206px;
    display: flex;
    align-items: center;
    gap: 10px;
  }
  .brand__dot {
    flex: none;
    width: 14px;
    height: 14px;
    border-radius: 50%;
    background: var(--cyan);
  }
  .brand__name {
    font-weight: 800;
    font-size: 17px;
    line-height: 1.2;
    letter-spacing: .03em;
    text-transform: uppercase;
    color: var(--text);
  }
  .divider {
    position: absolute;
    left: 256px;
    top: 70px;
    width: 1px;
    height: 120px;
    background: var(--rule);
  }
  .contact {
    position: absolute;
    left: 280px;
    top: 44px;
    color: var(--text);
  }
  .contact__name {
    margin: 0;
    font-weight: 800;
    font-size: 21px;
    letter-spacing: .03em;
    color: var(--cyan);
    text-transform: uppercase;
  }
  .contact__title {
    margin: 2px 0 12px;
    font-size: 13px;
    font-weight: 400;
  }
  .contact__address {
    margin: 0 0 10px;
    font-style: normal;
    font-size: 12.5px;
    line-height: 1.45;
  }
  .contact__list {
    list-style: none;
    margin: 0;
    padding: 0;
    font-size: 12.5px;
    line-height: 1.7;
  }
  .contact__list li {
    display: flex;
    align-items: center;
    gap: 8px;
  }
  .contact__list svg { flex: none; width: 11px; height: 11px; fill: var(--cyan); }
  .accent { color: var(--cyan); }

  .edge-band {
    position: absolute;
    left: 0;
    bottom: 0;
    width: 540px;
    height: 14px;
  }

  /* back */
  .pattern {
    position: absolute;
    inset: 0;
    background: linear-gradient(120deg, #111112 0%, #1f1f20 40%, #4c4c4e 75%, #8a8a8c 100%);
  }
</style>
</head>
<body>
<main class="stage">
  <section class="card card--front" aria-label="Business card front">
    <div class="brand">
      <span class="brand__dot"></span>
      <span class="brand__name">Bramblewood<br>Card Company</span>
    </div>

    <div class="divider"></div>

    <div class="contact">
      <h1 class="contact__name">Dorian Welk</h1>
      <p class="contact__title">CEO/Founder</p>
      <address class="contact__address">P.O. Box 3170 Lane<br>Fernhollow WA 8816</address>
      <ul class="contact__list">
        <li><svg viewBox="0 0 10 10"><path d="M2 0h2l1 3-1.5 1a6 6 0 0 0 2.5 2.5L7 5l3 1v2a2 2 0 0 1-2 2A8 8 0 0 1 0 2a2 2 0 0 1 2-2z"/></svg><span>(555) 318 2094</span></li>
        <li><svg viewBox="0 0 10 10"><path d="M0 2h10v6H0z M0 2l5 3.5L10 2"/></svg><span>info@bramblewoodcardco.com</span></li>
        <li><svg viewBox="0 0 10 10"><circle cx="5" cy="5" r="5"/></svg><span>www.<span class="accent">bramblewoodcardco</span>.com</span></li>
      </ul>
    </div>

    <svg class="edge-band" viewBox="0 0 540 14" preserveAspectRatio="none" aria-hidden="true">
      <polygon points="0,0 300,0 290,14 0,14" fill="var(--cyan)"/>
      <polygon points="300,0 540,0 540,14 290,14" fill="var(--grey)"/>
    </svg>
  </section>

  <section class="card card--back" aria-label="Business card back">
    <div class="pattern" role="img" aria-label="Repeating badge pattern of the brand emblem in graded greys, one badge picked out in cyan"></div>
  </section>
</main>
</body>
</html>
```